Cover Art Design for a Notebook

We are going to give away some note books to our marketing department and want an elegant art design for the cover. There is a theme centered around ABCD of marketing that we want to leverage in the design. So these letters should be prominent in the design. The ABCD stand for Agility, Boost, Customer, Data.

If you could Cleverly incorporate these words into the letters with a good design that would be good.

But please make the ABCD the focus of the artwork. The words associated with them should be subtle, in the background, visible but not the focus.

We are looking for stylish. We want people to feel proud of the ELEGANT DESIGN when they take out this notebook for business.

Also worth mentioning- We are a biotechnology company so if you incorporate elements in that theme in, on, or around the ABCD letters, it could be a good idea. As long as it doesn’t kill the rest of the design.

I will upload our logo for Kelvara Biolume Sciences later (you can see it online) and this will need to go in one corner.

Notebook will be A5 format. Image on front cover only. Need ASAP.

(Do not make baby blocks as we don’t want something that looks like a kids book)

Target Market(s)

business people who feel proud to pull out this notebook

Industry/Entity Type

Biotechnology

Colors
ec1f27
ffffff
000000

Requirements
Must have
• ELEGANT ART DESIGN USING ABCD
Nice to have
• see brief above
Should not have
• baby blocks

```html
<!DOCTYPE html>
<html lang="en">
<head>
<meta charset="utf-8">
<title>ABCD of Marketing — Notebook Cover</title>
<link rel="stylesheet" href="https://fonts.googleapis.com/css2?family=Fredoka:wght@700&family=Montserrat:wght@700&display=swap">
<style>
  :root {
    --cover-red: #ec1f27;
    --letter-deep: #5a0d12;
    --letter-mid: #a3161d;
    --letter-light: #c8242b;
    --word-tone: #f57a6c;
    --network-tone: rgba(255, 170, 200, 0.35);
    --white: #ffffff;
  }
  html, body {
    margin: 0;
    padding: 0;
    overflow: hidden;
    background: var(--cover-red);
  }
  .cover {
    position: relative;
    width: 849px;
    height: 1200px;
    background: var(--cover-red);
    overflow: hidden;
  }
  .network {
    position: absolute;
    border-radius: 50%;
  }
  .network--top-right {
    left: 600px;
    top: -20px;
    width: 300px;
    height: 340px;
    background: radial-gradient(ellipse at 70% 40%, var(--network-tone), transparent 68%);
  }
  .network--bottom-left {
    left: -80px;
    top: 720px;
    width: 420px;
    height: 520px;
    background: radial-gradient(ellipse at 35% 60%, var(--network-tone), transparent 68%);
  }
  .letters {
    position: absolute;
    inset: 0;
  }
  .letter-glyph {
    font-family: "Fredoka", "Arial Rounded MT Bold", sans-serif;
    font-weight: 700;
    font-size: 330px;
    fill: url(#cutout-depth);
  }
  .theme-word {
    position: absolute;
    margin: 0;
    font-family: "Montserrat", Arial, sans-serif;
    font-weight: 700;
    font-size: 29px;
    letter-spacing: 0.5px;
    color: var(--word-tone);
    transform: translateX(-50%);
    white-space: nowrap;
  }
  .theme-word--agility  { left: 249px; top: 486px; }
  .theme-word--boost    { left: 577px; top: 486px; }
  .theme-word--customer { left: 251px; top: 822px; }
  .theme-word--data     { left: 576px; top: 822px; }
  .brand {
    position: absolute;
    right: 70px;
    top: 1104px;
    display: flex;
    align-items: center;
    gap: 10px;
    margin: 0;
    color: var(--white);
    font-family: "Montserrat", Arial, sans-serif;
    font-weight: 700;
    font-size: 19px;
    line-height: 1;
    white-space: nowrap;
  }
  .brand__dot {
    width: 12px;
    height: 12px;
    border-radius: 50%;
    background: var(--white);
  }
</style>
</head>
<body>
  <main class="cover">
    <div class="network network--top-right" role="img" aria-label="Molecular network of connected dots and fine lines"></div>
    <div class="network network--bottom-left" role="img" aria-label="Molecular network of connected dots and fine lines"></div>

    <svg class="letters" width="849" height="1200" viewBox="0 0 849 1200" role="img" aria-label="Large paper-cut letters A, B, C and D revealing layered organic shapes inside">
      <defs>
        <linearGradient id="cutout-depth" x1="0" y1="0" x2="0.4" y2="1">
          <stop offset="0" stop-color="var(--letter-deep)"/>
          <stop offset="0.5" stop-color="var(--letter-mid)"/>
          <stop offset="1" stop-color="var(--letter-light)"/>
        </linearGradient>
      </defs>
      <text class="letter-glyph" x="262" y="458" text-anchor="middle">A</text>
      <text class="letter-glyph" x="582" y="458" text-anchor="middle">B</text>
      <text class="letter-glyph" x="258" y="796" text-anchor="middle">C</text>
      <text class="letter-glyph" x="580" y="796" text-anchor="middle">D</text>
    </svg>

    <p class="theme-word theme-word--agility">AGILITY</p>
    <p class="theme-word theme-word--boost">BOOST</p>
    <p class="theme-word theme-word--customer">CUSTOMER</p>
    <p class="theme-word theme-word--data">DATA</p>

    <p class="brand"><span class="brand__dot"></span>Kelvara Biolume Sciences</p>
  </main>
</body>
</html>
```